Web Design For Marlow Pool Service

We are working with a company that wants a website for their pool service. Some sites to use for content/competitors and inspiration:
https://sacramento.brightwaterpoolco.example/builder/newbuild/repair/ppc
https://hollowbrookpoolcareplus.example/
https://lakemontpoolservice.example/
https://www.dravenspoolresurfacing.example/pool-renovation-ga/
Thank you for taking the time to consider designing a website for us. We are web developers based in Stockton, CA, USA. Most of our projects go through the same process. Understanding this process may help you win a project with us. We custom-code all of our websites in-house. We don’t have any requirements as to what tools you use for your design, but we prefer Figma files. For any design that we label as four-stars, we send it to the client for review. The client picks the final design they want us to use. Once we complete this process, we will continue to show additional clients all the four-star sites and purchase them later. Your designs will have multiple chances to sell. For better chances of success, we ask that you follow these guidelines.
IMAGES:
If you use any images or icons in the design, we ask that you have a link to the asset so we can purchase the image/icon. Most of the designs we submit do not have the customer’s images on them unless they have some great images. Be creative; show us the feeling you are trying to portray with your image choices. Use any royalty-free site you choose. We subscribe to Adobe and mainly use their images, but we can purchase images outside of Adobe. PLEASE NOTE: we will not submit designs to clients with watermarks on the images.
FONTS:
We ask that you identify the fonts used in the design. This can be done in a message if you want. We typically use Google Fonts and Adobe Fonts.
CONTENT:
We're always open to different content and ideas. We often submit designs with stock images so the client can see our vision. We typically take pictures after the website launch to use their images with our vision. Lorem Ipsum is fine for paragraphs, but we ask that you write the headers in correct English. We want to be able to show the vision and identify the sections of the website.
INSPIRATION:
We typically add a couple of links in the brief of websites we like to help you get started in your design.
REVISIONS:
We do not often ask for revisions of the designs unless we see something in the design that may not appeal to the client. If there are slight changes that we want to make, we do that in the development process.
FEEDBACK:
We rarely give feedback on designs during the design process. We are working on many website projects and do not have the time to provide feedback. We usually respond if your request is well thought out and asks specific questions, but a note asking “feedback, please” usually goes unanswered.
Number of Pages Required
1 page
Look and feel
Each slider illustrates characteristics of the customer's brand and the style your logo design should communicate.

```html
<!DOCTYPE html>
<html lang="en">
<head>
<meta charset="utf-8">
<title>Marlow Pool Service</title>
<link href="https://fonts.googleapis.com/css2?family=Noto+Sans:wght@400;500;600;700&family=Open+Sans:wght@300;400;600;700&display=swap" rel="stylesheet">
<style>
:root{
  --navy:#1c3e72;
  --blue:#2f9bff;
  --blue-dark:#1877e0;
  --pale:#eef2f7;
  --ink:#3f4650;
  --muted:#6b7280;
  --dark:#1f2329;
  --white:#ffffff;
}
*{margin:0;padding:0;box-sizing:border-box}
html,body{width:1200px;height:4377px;overflow:hidden}
body{position:relative;font-family:"Open Sans",sans-serif;color:var(--ink);background:var(--white)}
.abs{position:absolute}
.heading{font-family:"Noto Sans",sans-serif;font-weight:600}
.eyebrow{font-size:13px;color:var(--blue);text-decoration:underline;text-underline-offset:4px;letter-spacing:.3px}
.center{left:0;width:1200px;text-align:center}
.btn{display:flex;align-items:center;justify-content:center;gap:12px;background:var(--blue);color:var(--white);font-weight:600;font-size:16px}
.brand{font-family:"Noto Sans",sans-serif;font-weight:500;color:var(--navy);display:flex;align-items:center;gap:8px;white-space:nowrap}
.brand-dot{width:14px;height:14px;border-radius:50%;background:var(--blue)}
.photo{position:absolute}

/* top */
.hero{left:0;top:0;width:1200px;height:800px;background:linear-gradient(180deg,#4f5a60 0%,#6a6f6a 35%,#8a7f72 65%,#6f6a65 100%)}
.hero-shade{left:0;top:0;width:1200px;height:800px;background:rgba(20,24,30,.35)}
.topbar{top:8px;font-size:12px;color:var(--white);display:flex;align-items:center;gap:6px}
.social-sq{width:14px;height:14px;background:var(--white);border-radius:2px}
.nav{left:87px;top:34px;width:1030px;height:85px;background:var(--white);border-radius:4px}
.nav-link{top:68px;font-size:13px;color:#222;font-weight:500;letter-spacing:.3px}
.hero-title{top:358px;font-family:"Open Sans",sans-serif;font-weight:400;font-size:70px;line-height:88px;color:var(--white)}

/* services */
.services-bg{left:0;top:748px;width:1200px;height:727px;background:var(--pale)}
.card{width:323px;height:221px;top:1040px;background:var(--white);border-radius:6px;box-shadow:0 6px 18px rgba(30,60,110,.08)}
.card-photo{top:1008px;width:289px;height:163px;border-radius:3px}
.card-icon{width:64px;height:64px;border-radius:50%;background:var(--navy);border:4px solid var(--white);display:flex;align-items:center;justify-content:center}
.card-label{top:1195px;font-size:12px;color:var(--blue);width:323px;text-align:center}
.card-title{top:1210px;font-size:29px;color:var(--navy);width:323px;text-align:center;font-weight:500}

/* about */
.about{left:0;top:1475px;width:1200px;height:556px;background:linear-gradient(135deg,#2b3138 0%,#30383a 40%,#3b4540 70%,#2a2f33 100%)}
.about-shade{left:0;top:1475px;width:1200px;height:556px;background:rgba(15,18,24,.45)}
.about p{font-size:14px;line-height:21px;color:#e7ebf0}

/* why */
.why-item-l{width:320px;text-align:right}
.why-item-r{width:320px}
.why-title{font-size:20px;color:var(--navy);font-weight:500;font-family:"Noto Sans",sans-serif}
.why-text{font-size:13px;line-height:21px;color:var(--muted);margin-top:4px}
.why-icon{width:58px;height:58px;border-radius:50%;background:var(--navy);border:3px solid var(--white);display:flex;align-items:center;justify-content:center;box-shadow:0 2px 6px rgba(0,0,0,.15)}

/* testimonials */
.testi{left:0;top:2740px;width:1200px;height:558px;background:linear-gradient(160deg,#2a2420 0%,#332c27 40%,#3a3a3c 70%,#25272b 100%)}
.quote{top:2929px;width:489px;height:189px;background:rgba(95,90,88,.85);border-radius:3px;padding:32px 20px 0}
.quote h3{font-family:"Noto Sans",sans-serif;font-weight:600;font-size:27px;color:var(--white)}
.quote p{margin-top:14px;font-size:14.5px;line-height:24px;color:#eceae8}
.quote-tail{width:0;height:0;border-left:13px solid transparent;border-right:13px solid transparent;border-top:14px solid rgba(95,90,88,.85)}
.avatar{width:64px;height:64px;border-radius:50%;background:linear-gradient(180deg,#c9c3bd,#6c6660);border:2px solid #ddd}
.who-name{font-family:"Noto Sans",sans-serif;font-weight:600;font-size:20px;color:var(--white)}
.who-role{font-size:14px;color:#e4e4e4;margin-top:6px}
.dot{top:3258px;width:12px;height:12px;border-radius:50%;background:var(--white)}

/* contact */
.contact-card{left:139px;top:3519px;width:920px;height:459px;background:var(--white);border-radius:10px;box-shadow:0 10px 30px rgba(0,0,0,.12);overflow:hidden}
.field{position:absolute;border:1px solid #cfd5dc;border-radius:3px;font-size:12px;color:#555;padding:10px 8px}

/* footer */
.foot-link{top:4140px;font-size:14px;color:var(--white);font-weight:500}
.foot-circle{width:58px;height:58px;border-radius:50%;border:1.5px solid #d5d5d5;display:flex;align-items:center;justify-content:center}
.foot-text{font-size:12px;line-height:17px;color:var(--white)}
.bottom{left:0;top:4322px;width:1200px;height:55px;background:var(--blue)}
.sq{width:24px;height:24px;border:1.5px solid var(--white);border-radius:2px}
</style>
</head>
<body>

<!-- HERO -->
<div class="abs hero photo" role="img" aria-label="Photo of children running with swim rings toward a backyard pool"></div>
<div class="abs hero-shade"></div>

<div class="abs topbar" style="left:102px">
  <svg width="10" height="13" viewBox="0 0 10 13"><path d="M5 0a5 5 0 0 0-5 5c0 3.6 5 8 5 8s5-4.4 5-8a5 5 0 0 0-5-5zm0 7a2 2 0 1 1 0-4 2 2 0 0 1 0 4z" fill="#fff"/></svg>
  1233 Some Street , City
</div>
<div class="abs topbar" style="left:362px">
  <svg width="13" height="9" viewBox="0 0 13 9"><rect width="13" height="9" fill="#fff"/><path d="M0 0l6.5 5L13 0" stroke="#555" fill="none"/></svg>
  hello@marlowpool.example
</div>
<div class="abs topbar" style="left:578px">
  <svg width="11" height="11" viewBox="0 0 24 24"><path d="M6.6 10.8a15.1 15.1 0 0 0 6.6 6.6l2.2-2.2a1 1 0 0 1 1-.25 11.4 11.4 0 0 0 3.6.57 1 1 0 0 1 1 1V20a1 1 0 0 1-1 1A17 17 0 0 1 3 4a1 1 0 0 1 1-1h3.5a1 1 0 0 1 1 1c0 1.25.2 2.45.57 3.57a1 1 0 0 1-.25 1z" fill="#fff"/></svg>
  123 - 123 - 1234
</div>
<div class="abs topbar" style="left:1002px;gap:13px">
  <div class="social-sq"></div><div class="social-sq"></div><div class="social-sq"></div><div class="social-sq"></div>
</div>

<div class="abs nav"></div>
<div class="abs brand" style="left:136px;top:62px;font-size:21px"><span class="brand-dot"></span>Marlow Pool Service</div>
<div class="abs nav-link" style="left:434px">HOME</div>
<div class="abs nav-link" style="left:534px">ABOUT US</div>
<div class="abs nav-link" style="left:671px">SERVICES</div>
<div class="abs nav-link" style="left:796px">CONTACT US</div>

<div class="abs center" style="top:321px;font-size:17px;color:var(--white)">Welcome</div>
<h1 class="abs center hero-title">Crafting Memories,<br>One Pool at a Time</h1>
<div class="abs btn" style="left:524px;top:592px;width:155px;height:42px;font-size:15px">Contact us
  <svg width="18" height="12" viewBox="0 0 18 12"><path d="M0 6h16M11 1l5 5-5 5" stroke="#fff" stroke-width="1.6" fill="none"/></svg>
</div>

<!-- SERVICES -->
<div class="abs services-bg"></div>
<svg class="abs" style="left:0;top:680px" width="1200" height="140" viewBox="0 0 1200 140">
  <path d="M0 68 C80 22 260 10 460 40 C520 50 560 70 610 80 C520 100 380 118 250 108 C150 100 60 84 0 68 Z" fill="var(--blue)"/>
  <path d="M0 72 C120 118 330 126 500 96 C700 60 860 120 1000 118 C1100 116 1160 90 1200 70 L1200 140 L0 140 Z" fill="var(--pale)"/>
</svg>

<div class="abs center eyebrow" style="top:856px">WHAT WE DO</div>
<h2 class="abs center heading" style="top:895px;font-size:48px;color:var(--navy)">Services We Offer</h2>

<div class="abs card" style="left:85px"></div>
<div class="abs card" style="left:437px"></div>
<div class="abs card" style="left:787px"></div>

<div class="abs card-photo photo" style="left:102px;background:linear-gradient(135deg,#4aa7d8,#8ccbe6 50%,#2e6f9a)" role="img" aria-label="Photo of a technician repairing pool tiles"></div>
<div class="abs card-photo photo" style="left:454px;background:linear-gradient(135deg,#8c99a6,#c8ccc9 50%,#6f7a5a)" role="img" aria-label="Photo of a construction team in hard hats"></div>
<div class="abs card-photo photo" style="left:804px;background:linear-gradient(135deg,#3d8fb8,#6cc3d9 50%,#c98b6a)" role="img" aria-label="Photo of a family relaxing in a sunny pool"></div>

<div class="abs card-icon" style="left:329px;top:1106px"><svg width="26" height="26" viewBox="0 0 24 24"><path d="M12 3l2.6 5.4 5.9.8-4.3 4.1 1 5.9L12 16.4 6.8 19.2l1-5.9L3.5 9.2l5.9-.8z" stroke="#fff" stroke-width="1.6" fill="none"/></svg></div>
<div class="abs card-icon" style="left:680px;top:1106px"><svg width="26" height="26" viewBox="0 0 24 24"><circle cx="12" cy="12" r="8" stroke="#fff" stroke-width="1.6" fill="none"/><path d="M9 9l6 6M15 9l-6 6" stroke="#fff" stroke-width="1.6"/></svg></div>
<div class="abs card-icon" style="left:1031px;top:1106px"><svg width="26" height="26" viewBox="0 0 24 24"><path d="M4 20h16M7 17l4-9 4 4 3-8" stroke="#fff" stroke-width="1.6" fill="none"/></svg></div>

<div class="abs card-label" style="left:85px">OUR SERVICES</div>
<div class="abs card-label" style="left:437px">OUR SERVICES</div>
<div class="abs card-label" style="left:787px">OUR SERVICES</div>
<div class="abs card-title heading" style="left:85px">Pool Repair</div>
<div class="abs card-title heading" style="left:437px">Pool Construction</div>
<div class="abs card-title heading" style="left:787px">Pool Cleaning</div>

<div class="abs center" style="top:1318px;font-size:19px;color:#666">The demanded experts in your area</div>
<div class="abs btn" style="left:490px;top:1365px;width:217px;height:63px;background:var(--white);color:var(--blue);font-size:23px;font-weight:500;box-shadow:0 4px 14px rgba(0,0,0,.08)">Contact us
  <svg width="26" height="18" viewBox="0 0 26 18"><path d="M0 9h24M16 1l8 8-8 8" stroke="var(--blue)" stroke-width="2" fill="none"/></svg>
</div>

<!-- ABOUT -->
<div class="abs about photo" role="img" aria-label="Photo of a dusk-lit backyard with palms and loungers"></div>
<div class="abs about-shade"></div>
<div class="abs" style="left:125px;top:1535px;width:380px;height:390px;background:var(--navy);border-radius:26px;transform:rotate(-7deg)"></div>
<div class="abs photo" style="left:112px;top:1560px;width:381px;height:373px;border-radius:26px;background:linear-gradient(135deg,#a9b4bd,#d6d8d6 40%,#b73a36 70%,#4b5b6a)" role="img" aria-label="Photo of a technician with a tool case beside a pool deck"></div>

<div class="abs" style="left:610px;top:1533px;font-size:13px;color:var(--white);text-decoration:underline;text-underline-offset:4px">WHO WE ARE</div>
<h2 class="abs heading" style="left:610px;top:1570px;font-size:41px;line-height:52px;color:var(--white);font-weight:700">Crafting Aquatic<br>Masterpieces</h2>
<div class="abs heading" style="left:610px;top:1698px;font-size:22px;color:var(--white);font-weight:500">Inspired Designs, Impeccable Craftsmanship</div>
<div class="abs" style="left:610px;top:1744px;width:515px">
  <p>Lorem ipsum dolor sit amet, consectetur adipiscing elit, sed do eiusmod temp or incididunt ut labore et dolore magna aliqua. Ut enim ad minim veniam, quis laboris nisi ut aliquip ex ea commodo consequat.</p>
  <p style="margin-top:12px">Lorem ipsum dolor sit amet, consectetur adipiscing elit, sed do eiusmod temp or incididunt ut labore et dolore magna aliqua.</p>
</div>
<div class="abs btn" style="left:609px;top:1904px;width:155px;height:42px;justify-content:flex-start;padding-left:16px;font-size:15px">Contact us</div>

<!-- WHY -->
<div class="abs center eyebrow" style="top:2096px">WHY US</div>
<h2 class="abs center heading" style="top:2128px;font-size:42px;color:var(--navy)">Why Choose Us</h2>

<svg class="abs" style="left:405px;top:2232px" width="380" height="380" viewBox="0 0 380 380">
  <circle cx="190" cy="190" r="186" fill="none" stroke="#333" stroke-width="1.5" stroke-dasharray="5 4"/>
  <circle cx="190" cy="190" r="156" fill="#d9d8f3"/>
</svg>
<div class="abs photo" style="left:449px;top:2276px;width:292px;height:292px;border-radius:50%;background:linear-gradient(180deg,#eceef2 0%,#b58a68 45%,#202633 80%)" role="img" aria-label="Photo of a smiling business woman with arms crossed"></div>

<div class="abs why-icon" style="left:413px;top:2330px"><svg width="24" height="24" viewBox="0 0 24 24"><path d="M4 14a8 8 0 0 1 16 0M4 14v4h3v-5H4M20 14v4h-3v-5h3" stroke="#fff" stroke-width="1.6" fill="none"/></svg></div>
<div class="abs why-icon" style="left:387px;top:2434px"><svg width="24" height="24" viewBox="0 0 24 24"><path d="M12 3l2.6 5.4 5.9.8-4.3 4.1 1 5.9L12 16.4 6.8 19.2l1-5.9L3.5 9.2l5.9-.8z" stroke="#fff" stroke-width="1.6" fill="none"/></svg></div>
<div class="abs why-icon" style="left:432px;top:2531px"><svg width="24" height="24" viewBox="0 0 24 24"><circle cx="8" cy="8" r="3" stroke="#fff" stroke-width="1.6" fill="none"/><circle cx="16" cy="8" r="3" stroke="#fff" stroke-width="1.6" fill="none"/><path d="M3 19c0-3 2-5 5-5s5 2 5 5M11 19c0-3 2-5 5-5s5 2 5 5" stroke="#fff" stroke-width="1.6" fill="none"/></svg></div>
<div class="abs why-icon" style="left:731px;top:2330px"><svg width="24" height="24" viewBox="0 0 24 24"><path d="M19 12a7 7 0 0 1-12 5M5 12a7 7 0 0 1 12-5M17 3v4h-4M7 21v-4h4" stroke="#fff" stroke-width="1.6" fill="none"/></svg></div>
<div class="abs why-icon" style="left:755px;top:2434px"><svg width="24" height="24" viewBox="0 0 24 24"><path d="M4 20h16M7 17l4-9 4 4 3-8" stroke="#fff" stroke-width="1.6" fill="none"/></svg></div>
<div class="abs why-icon" style="left:710px;top:2531px"><svg width="24" height="24" viewBox="0 0 24 24"><path d="M19 12a7 7 0 0 1-12 5M5 12a7 7 0 0 1 12-5M17 3v4h-4M7 21v-4h4" stroke="#fff" stroke-width="1.6" fill="none"/></svg></div>

<div class="abs why-item-l" style="left:48px;top:2323px"><div class="why-title">Quality Assurance</div><div class="why-text">Lorem ipsum dolor sit amet,<br>consectetur adipiscing elit, sed<br>do eiusmod tempor incididunt</div></div>
<div class="abs why-item-l" style="left:30px;top:2437px"><div class="why-title">Proven Record</div><div class="why-text">Lorem ipsum dolor sit amet,<br>consectetur adipiscing elit, sed<br>do eiusmod tempor incididunt</div></div>
<div class="abs why-item-l" style="left:68px;top:2548px"><div class="why-title">Personalized Approach</div><div class="why-text">Lorem ipsum dolor sit amet,<br>consectetur adipiscing elit, sed<br>do eiusmod tempor incididunt</div></div>
<div class="abs why-item-r" style="left:830px;top:2304px"><div class="why-title">Comprehensive Services</div><div class="why-text">Lorem ipsum dolor sit amet,<br>consectetur adipiscing elit, sed<br>do eiusmod tempor incididunt</div></div>
<div class="abs why-item-r" style="left:848px;top:2423px"><div class="why-title">Professionalism</div><div class="why-text">Lorem ipsum dolor sit amet,<br>consectetur adipiscing elit, sed<br>do eiusmod tempor incididunt</div></div>
<div class="abs why-item-r" style="left:806px;top:2548px"><div class="why-title">Experience and expertise</div><div class="why-text">Lorem ipsum dolor sit amet,<br>consectetur adipiscing elit, sed<br>do eiusmod tempor incididunt</div></div>

<!-- TESTIMONIALS -->
<div class="abs testi photo" role="img" aria-label="Photo of a dim poolside lounge at night"></div>
<div class="abs" style="left:88px;top:2788px;font-size:13px;color:var(--white);text-decoration:underline;text-underline-offset:4px">TESTIMONIALS</div>
<h2 class="abs heading" style="left:88px;top:2822px;font-size:41px;color:var(--white)">What our clients are saying</h2>
<div class="abs" style="left:915px;top:2839px;font-size:15px;color:var(--white);font-weight:500">More Testimonials</div>
<div class="abs" style="left:1064px;top:2830px;width:38px;height:38px;background:var(--blue);display:flex;align-items:center;justify-content:center"><svg width="10" height="14" viewBox="0 0 10 14"><path d="M2 1l6 6-6 6" stroke="#fff" stroke-width="2" fill="none"/></svg></div>

<div class="abs quote" style="left:92px"><h3>Their service was excellent</h3><p>Lorem ipsum dolor sit amet, consectetur adipiscing elit, sed do eiusmod tempor incididunt ut labore et dolore magna aliqua. Ut enim ad minim</p></div>
<div class="abs quote" style="left:614px"><h3>Their service was excellent</h3><p>Lorem ipsum dolor sit amet, consectetur adipiscing elit, sed do eiusmod tempor incididunt ut labore et dolore magna aliqua. Ut enim ad minim</p></div>
<div class="abs quote-tail" style="left:128px;top:3118px"></div>
<div class="abs quote-tail" style="left:650px;top:3118px"></div>

<div class="abs avatar photo" style="left:109px;top:3152px" role="img" aria-label="Client portrait photo"></div>
<div class="abs" style="left:199px;top:3157px"><div class="who-name">Nora Keane</div><div class="who-role">Client</div></div>
<div class="abs avatar photo" style="left:631px;top:3152px" role="img" aria-label="Client portrait photo"></div>
<div class="abs" style="left:721px;top:3157px"><div class="who-name">Owen Pratt</div><div class="who-role">Client</div></div>

<div class="abs dot" style="left:586px;background:var(--blue)"></div>
<div class="abs dot" style="left:608px"></div>
<div class="abs dot" style="left:630px"></div>

<!-- CONTACT -->
<div class="abs center eyebrow" style="top:3368px">CONTACT US</div>
<h2 class="abs center heading" style="top:3400px;font-size:42px;color:var(--navy)">Get in touch with us</h2>

<svg class="abs" style="left:0;top:3740px" width="1200" height="582" viewBox="0 0 1200 582">
  <path d="M0 150 C80 80 180 40 260 30 L1060 30 L1060 110 C1110 130 1160 160 1200 190 L1200 582 L0 582 Z" fill="#1d1f22"/>
  <path d="M1060 100 C1110 118 1165 150 1200 178 L1200 220 C1160 186 1110 150 1060 130 Z" fill="var(--blue)"/>
</svg>
<div class="abs photo" style="left:0;top:3875px;width:1200px;height:447px;background:linear-gradient(180deg,rgba(40,42,46,.0),rgba(60,62,66,.35))" role="img" aria-label="Faint photo of a pool skimmer and ladder"></div>

<div class="abs contact-card">
  <div class="photo" style="left:0;top:0;width:468px;height:459px;background:linear-gradient(135deg,#27a7cf 0%,#6fd0e6 40%,#a1683f 70%,#6e4b34 100%)" role="img" aria-label="Photo of a woman in a sun hat sitting at the pool edge"></div>
</div>
<div class="abs brand" style="left:655px;top:3580px;font-size:17px"><span class="brand-dot" style="width:11px;height:11px"></span>Marlow Pool Service</div>
<div class="abs" style="left:649px;top:3627px;font-size:30px;color:#333;font-family:'Open Sans',sans-serif">Please fill out the form</div>
<div class="field" style="left:649px;top:3692px;width:362px;height:34px">Name</div>
<div class="field" style="left:649px;top:3743px;width:174px;height:37px">Phone</div>
<div class="field" style="left:835px;top:3743px;width:176px;height:37px">Email</div>
<div class="field" style="left:649px;top:3796px;width:362px;height:69px">Message</div>
<div class="abs btn" style="left:649px;top:3882px;width:362px;height:38px;font-size:13px;border-radius:3px">Send</div>

<!-- FOOTER -->
<div class="abs center" style="top:4046px;display:flex;justify-content:center">
  <div class="brand" style="color:var(--white);font-size:26px"><span class="brand-dot" style="width:16px;height:16px;background:var(--white)"></span>Marlow Pool Service</div>
</div>
<div class="abs foot-link" style="left:352px">HOME</div>
<div class="abs foot-link" style="left:446px">SERVICES</div>
<div class="abs foot-link" style="left:552px">ABOUT US</div>
<div class="abs foot-link" style="left:671px">TESTIMONIALS</div>
<div class="abs foot-link" style="left:820px">BLOG</div>
<div class="abs" style="left:139px;top:4194px;width:920px;height:1px;background:#8a8a8a"></div>

<div class="abs foot-circle" style="left:171px;top:4234px"><svg width="30" height="30" viewBox="0 0 24 24"><circle cx="12" cy="12" r="9" stroke="#fff" stroke-width="1.3" fill="none"/><path d="M3 12h18M12 3c3 3 3 15 0 18M12 3c-3 3-3 15 0 18" stroke="#fff" stroke-width="1.3" fill="none"/></svg></div>
<div class="abs foot-text" style="left:241px;top:4248px">123, Building Name, Street<br>City, State XY 123456</div>
<div class="abs" style="left:430px;top:4234px;width:1px;height:58px;background:#8a8a8a"></div>
<div class="abs foot-circle" style="left:503px;top:4234px"><svg width="26" height="30" viewBox="0 0 24 24"><rect x="7" y="3" width="10" height="18" rx="2" stroke="#fff" stroke-width="1.3" fill="none"/><path d="M11 18h2" stroke="#fff" stroke-width="1.3"/></svg></div>
<div class="abs foot-text" style="left:573px;top:4246px;font-size:13px">PHONE<br>(123) 456 7890</div>
<div class="abs" style="left:750px;top:4234px;width:1px;height:58px;background:#8a8a8a"></div>
<div class="abs foot-circle" style="left:826px;top:4234px"><svg width="28" height="28" viewBox="0 0 24 24"><rect x="3" y="6" width="18" height="13" stroke="#fff" stroke-width="1.3" fill="none"/><path d="M3 6l9 7 9-7" stroke="#fff" stroke-width="1.3" fill="none"/></svg></div>
<div class="abs foot-text" style="left:896px;top:4246px;font-size:13px">EMAIL<br>info@marlowpool.example</div>

<div class="abs bottom"></div>
<div class="abs" style="left:148px;top:4340px;font-size:13px;color:var(--white)">Marlow Pool Services</div>
<div class="abs" style="left:933px;top:4337px;display:flex;gap:8px">
  <div class="sq"></div><div class="sq"></div><div class="sq"></div><div class="sq"></div>
</div>

</body>
</html>
```